PERI VALORE

We need a letterhead design for an Image & Etiquette Consultancy company based in Singapore.

The services we provide are Personal Image Consultation, Image & Etiquette Workshop for schools and corporate.

The design should have our corporate colour as seen in the logo files I have uploaded.

Since our company helps clients with their image, the design should be aesthetically very appealing. It should reflect a very classy & elegant feel.

I will print the letterhead using my printer but most of the time will use it to write letters to my clients therefore the format should include MS Word.

```html
<!DOCTYPE html>
<html lang="en">
<head>
<meta charset="utf-8">
<title>Peri Valore Letterhead</title>
<link href="https://fonts.googleapis.com/css2?family=Michroma&family=Roboto:wght@400&display=swap" rel="stylesheet">
<style>
  :root{
    --backdrop:#e6e6e6;
    --paper:#ffffff;
    --plum:#4a1f5c;
    --gold:#d0a62f;
    --ink:#3a3a3a;
  }
  html,body{margin:0;padding:0;width:1200px;height:795px;overflow:hidden;background:var(--backdrop);}
  .letterhead{
    position:absolute;left:340px;top:28px;width:520px;height:738px;
    background:var(--paper);box-shadow:0 4px 18px rgba(0,0,0,.12);overflow:hidden;
  }
  .brand-band{
    position:absolute;left:0;top:52px;width:282px;height:36px;background:var(--plum);
    display:flex;flex-direction:column;justify-content:center;align-items:flex-end;padding-right:10px;box-sizing:border-box;
  }
  .brand-name{
    font-family:'Michroma',sans-serif;font-size:16px;line-height:1;color:var(--gold);letter-spacing:1px;
  }
  .brand-tagline{
    font-family:'Roboto',sans-serif;font-size:5px;color:var(--gold);letter-spacing:1.2px;margin-top:3px;
  }
  .contact{
    position:absolute;left:292px;top:34px;font-family:'Roboto',sans-serif;font-size:5.5px;line-height:1.35;color:var(--ink);
  }
  .contact-row{display:flex;align-items:flex-start;gap:5px;margin-bottom:4px;}
  .contact-row svg{width:6px;height:6px;flex:none;margin-top:1px;fill:var(--plum);}
  .contact-group .contact-row{margin-bottom:0;}
  .corner-tab{position:absolute;right:0;top:0;width:32px;height:8px;background:var(--plum);}
  .footer-rule-gold{position:absolute;left:0;bottom:0;width:372px;height:3px;background:var(--gold);}
  .footer-rule-plum{position:absolute;left:372px;right:0;bottom:0;height:4px;background:var(--plum);}
</style>
</head>
<body>
  <main class="letterhead">
    <div class="corner-tab"></div>

    <header class="brand-band">
      <div class="brand-name">PERI VALORE</div>
      <div class="brand-tagline">IMAGE AND ETIQUETTE CONSULTANCY</div>
    </header>

    <address class="contact" style="font-style:normal">
      <div class="contact-row">
        <svg viewBox="0 0 10 10"><path d="M5 0a3.5 3.5 0 0 0-3.5 3.5C1.5 6 5 10 5 10s3.5-4 3.5-6.5A3.5 3.5 0 0 0 5 0zm0 5a1.5 1.5 0 1 1 0-3 1.5 1.5 0 0 1 0 3z"/></svg>
        <span>What ever your street No. 12<br>Your city, postal code</span>
      </div>
      <div class="contact-group">
        <div class="contact-row">
          <svg viewBox="0 0 10 10"><path d="M2 0h2l1 3-1.5 1a6 6 0 0 0 2.5 2.5L7 5l3 1v2a2 2 0 0 1-2 2A8 8 0 0 1 0 2a2 2 0 0 1 2-2z"/></svg>
          <span>0 123 4567 789</span>
        </div>
        <div class="contact-row">
          <svg viewBox="0 0 10 10"><path d="M0 2h10v6H0z M0 2l5 3.5L10 2" stroke="#fff" stroke-width=".6"/></svg>
          <span>info@perivalore.com</span>
        </div>
        <div class="contact-row">
          <svg viewBox="0 0 10 10"><circle cx="5" cy="5" r="5"/><path d="M0 5h10M5 0c-2.5 3-2.5 7 0 10M5 0c2.5 3 2.5 7 0 10" stroke="#fff" stroke-width=".6" fill="none"/></svg>
          <span>www.perivalore.com</span>
        </div>
      </div>
    </address>

    <div class="footer-rule-gold"></div>
    <div class="footer-rule-plum"></div>
  </main>
</body>
</html>
```